Coastal Learner Bureau business cards

Australian company about to start offering its services. We recruit international students to come to study English, vocational education and postgraduate courses in Australia. We help them find the institution and select the right city they want to come to Australia. We are a young, online oriented and supportive agency. Our clients are between 18 and 35 years old, mainly University students, young professionals or people with work experience. We provide much more information that any other agency offer. We administrate a Facebook group with more than 11.000 members that daily ask questions about general information when coming to Australia, while they are here and even after they leave the country

Target Market(s)

International students from South America, Central America and Europe

Industry/Entity Type

Student

Contact Information for Business Card

Tomas Bilbrea
Managing Director
tomas@kelvarin.com.au
www.kelvoria.com.au
+61 491058264
Melbourne, Australia

Font styles to use
Serif
Sans Serif

Colors

Designer to choose colors to be used in the design.

Requirements
Must have
• Horizontal design
• Standard business card size and shape. If font uses green or yellow colours, they will have to match the ones from the logo
Nice to have
• UPDATE: Use the contents of the green image to design one of the card sides. Use our logo in the background of that side as watermark.
• Passport image, or immigration stamps. A picture of the Yarra River (from Melbourne) would be cool as well.
Should not have
• Non-standard business card size and shape
• Not black as the background colour of any sides as we are not a VIP agency or a hight class service. We are orientes to young people and they like colours, pictures, something attractive.
• Vertical design
• NO YELLOW or BLACK AS THE BACKGROUND COLOUR OF ANY SIDE OF THE BIZ CARD

```html
<!DOCTYPE html>
<html lang="en">
<head>
<meta charset="utf-8">
<title>Coastal Learner Bureau business cards</title>
<link href="https://fonts.googleapis.com/css2?family=Open+Sans:wght@400;600;700&display=swap" rel="stylesheet">
<style>
  :root {
    --backdrop: #3a3431;
    --card-front: #1f7a3d;
    --card-back: #1d5f8f;
    --gold: #f2c21b;
    --ink: #ffffff;
    --muted: #e3efe6;
    --divider: rgba(255,255,255,0.28);
  }
  * { margin: 0; padding: 0; box-sizing: border-box; }
  html, body { width: 1200px; height: 899px; overflow: hidden; }
  body {
    background: var(--backdrop);
    font-family: "Open Sans", Arial, sans-serif;
    position: relative;
  }
  .card {
    position: absolute;
    top: 302px;
    width: 530px;
    height: 295px;
    border-radius: 3px;
    box-shadow: 0 14px 30px rgba(0,0,0,0.45);
  }
  .card--front { left: 50px; background: var(--card-front); }
  .card--back {
    left: 620px;
    background: linear-gradient(135deg, var(--card-back), #2a7fb0);
  }

  .front-brand {
    position: absolute;
    left: 40px;
    top: 0;
    height: 100%;
    width: 230px;
    display: flex;
    align-items: center;
    gap: 10px;
  }
  .brand-dot {
    width: 16px; height: 16px;
    border-radius: 50%;
    background: var(--ink);
    flex: none;
  }
  .brand-name {
    font-size: 36px;
    font-weight: 700;
    color: var(--gold);
    letter-spacing: 0.5px;
  }
  .front-divider {
    position: absolute;
    left: 285px; top: 60px; bottom: 60px;
    width: 1px;
    background: var(--divider);
  }
  .contact {
    position: absolute;
    left: 305px;
    top: 62px;
    color: var(--ink);
  }
  .contact-name {
    font-size: 17px;
    font-weight: 700;
    color: var(--gold);
    line-height: 1.2;
  }
  .contact-role {
    font-size: 12.5px;
    color: var(--muted);
    margin-bottom: 22px;
  }
  .contact-city {
    font-size: 13px;
    margin-bottom: 16px;
  }
  .contact-list { list-style: none; }
  .contact-list li {
    display: flex;
    align-items: center;
    gap: 9px;
    font-size: 13px;
    line-height: 23px;
  }
  .contact-icon { width: 11px; height: 11px; flex: none; }
  .contact-icon .solid { fill: var(--gold); }
  .contact-icon .line { fill: none; stroke: var(--gold); stroke-width: 2.4; }

  .back-brand {
    position: absolute;
    left: 0; right: 0; top: 100px;
    text-align: center;
    font-size: 40px;
    font-weight: 700;
    color: var(--ink);
    letter-spacing: 0.5px;
  }
  .back-tagline {
    position: absolute;
    left: 0; right: 0; top: 200px;
    text-align: center;
    font-size: 14px;
    color: var(--ink);
    letter-spacing: 0.3px;
  }
</style>
</head>
<body>
  <section class="card card--front" aria-label="Business card front">
    <div class="front-brand">
      <span class="brand-dot"></span>
      <span class="brand-name">Kelvoria</span>
    </div>
    <div class="front-divider"></div>
    <div class="contact">
      <p class="contact-name">Tomas Bilbrea</p>
      <p class="contact-role">Managing Director</p>
      <p class="contact-city">Melbourne, Australia</p>
      <ul class="contact-list">
        <li>
          <svg class="contact-icon" viewBox="0 0 24 24" aria-hidden="true"><path class="solid" d="M6.6 10.8a15.1 15.1 0 0 0 6.6 6.6l2.2-2.2a1 1 0 0 1 1-.25 11.4 11.4 0 0 0 3.6.57 1 1 0 0 1 1 1V20a1 1 0 0 1-1 1A17 17 0 0 1 3 4a1 1 0 0 1 1-1h3.5a1 1 0 0 1 1 1c0 1.25.2 2.45.57 3.57a1 1 0 0 1-.25 1z"/></svg>
          +61 491058264
        </li>
        <li>
          <svg class="contact-icon" viewBox="0 0 24 24" aria-hidden="true"><rect class="line" x="2" y="5" width="20" height="14"/><path class="line" d="M2 5l10 8 10-8"/></svg>
          tomas@kelvarin.com.au
        </li>
        <li>
          <svg class="contact-icon" viewBox="0 0 24 24" aria-hidden="true"><circle class="line" cx="12" cy="12" r="10"/><path class="line" d="M2 12h20M12 2c3.5 3 3.5 17 0 20M12 2c-3.5 3-3.5 17 0 20"/></svg>
          www.kelvoria.com.au
        </li>
      </ul>
    </div>
  </section>

  <section class="card card--back" aria-label="Business card back">
    <p class="back-brand">Kelvoria</p>
    <p class="back-tagline">Hacemos más por ti!</p>
  </section>
</body>
</html>
```